Garlic Farm for Farm Sales/Restaurant sales

Need a professional, but appealing to agriculture world. We are selling 27 kinds of Organic Garlic from a farm in Simla,CO. I have uploaded logo and business information-we are going to need a template, because I will need to use it for four separate people.
-We are trying to appeal to Farm to table restaurants
-As well as growers/farmers

Target Market(s)

Agriculture Sales/Restaurants-Organic

Industry/Entity Type

Agriculture

Contact Information for Business Card

Want it to look more unique then your average kelto stock card- I want it to look amazing

Font styles to use
Sans Serif

Colors
0455a3
ec1f27
fbed22
ffffff

Requirements
Must have
• Just be creative
Nice to have
• Colorful
Should not have
• plain

```html
<!DOCTYPE html>
<html lang="en">
<head>
<meta charset="utf-8">
<title>Sky Mesa Gourmet Garlic – Business Card</title>
<link href="https://fonts.googleapis.com/css2?family=Open+Sans:ital,wght@0,400;0,600;0,700;1,400&display=swap" rel="stylesheet">
<style>
  :root {
    --navy: #062a5c;
    --red: #c00a2e;
    --yellow: #fdd800;
    --white: #ffffff;
    --ink: #4a4a4a;
    --rule: #b9b9b9;
    --backdrop: #e9e6e2;
  }
  * { box-sizing: border-box; margin: 0; padding: 0; }
  html, body { width: 1200px; height: 987px; overflow: hidden; }
  body {
    background: var(--backdrop);
    font-family: "Open Sans", Arial, sans-serif;
    position: relative;
  }
  .card {
    position: absolute;
    left: 292px;
    width: 617px;
    height: 352px;
    overflow: hidden;
    box-shadow: 0 2px 6px rgba(0,0,0,.25);
  }
  .card-front { top: 130px; background: var(--white); }
  .card-back { top: 505px; background: var(--red); }

  /* front */
  .brand-mark {
    position: absolute;
    left: 442px; top: 17px;
    width: 80px; height: 80px;
    border-radius: 50%;
    background: var(--red);
  }
  .brand-name {
    position: absolute;
    right: 24px; top: 106px;
    text-align: right;
    color: var(--navy);
    font-weight: 600;
    line-height: 1.1;
  }
  .brand-name .primary { display: block; font-size: 30px; }
  .brand-name .secondary { display: block; font-size: 13px; letter-spacing: .5px; }

  .person { position: absolute; left: 22px; top: 195px; }
  .person-name { color: var(--navy); font-weight: 600; font-size: 21px; line-height: 1.2; }
  .person-title { color: var(--red); font-size: 16px; line-height: 1.3; }

  .divider {
    position: absolute; left: 22px; top: 248px;
    width: 573px; height: 1px; background: var(--rule);
  }
  .contact { position: absolute; left: 22px; top: 256px; color: var(--ink); font-size: 15px; line-height: 23px; }
  .contact-row { display: flex; align-items: center; gap: 8px; }
  .contact-row svg { width: 14px; height: 14px; fill: var(--navy); }

  .address {
    position: absolute; right: 22px; top: 256px;
    text-align: right; color: var(--ink); font-size: 15px; line-height: 23px;
  }
  .footer-band { position: absolute; left: 0; bottom: 0; width: 617px; height: 36px; }
  .website {
    position: absolute; right: 22px; bottom: 7px;
    color: var(--white); font-style: italic; font-size: 15px; letter-spacing: 2.5px;
  }

  /* back */
  .back-panel {
    position: absolute; top: 0; right: 0;
    width: 159px; height: 352px; background: var(--navy);
  }
  .garlic-art {
    position: absolute; left: 291px; top: 11px;
    width: 261px; height: 330px;
    background: var(--yellow);
    border-radius: 50% 50% 46% 46% / 34% 34% 66% 66%;
  }
  .back-brand {
    position: absolute; left: 20px; top: 228px;
    color: var(--white); font-weight: 600; line-height: 1.1;
  }
  .back-brand .primary { display: block; font-size: 34px; }
  .back-brand .secondary { display: block; font-size: 14px; letter-spacing: .5px; padding-left: 4px; }
  .social { position: absolute; left: 88px; top: 311px; display: flex; gap: 4px; }
  .social-dot {
    width: 20px; height: 20px; border-radius: 50%;
    border: 1.5px solid var(--white);
  }
</style>
</head>
<body>

<section class="card card-front" aria-label="Business card front">
  <div class="brand-mark" aria-hidden="true"></div>
  <div class="brand-name">
    <span class="primary">Sky Mesa</span>
    <span class="secondary">Gourmet Garlic</span>
  </div>

  <div class="person">
    <p class="person-name">DANIEL REYES</p>
    <p class="person-title">CEO/FOUNDER</p>
  </div>

  <div class="divider"></div>

  <div class="contact">
    <p class="contact-row">
      <svg viewBox="0 0 24 24" aria-hidden="true"><path d="M6.6 10.8a15.1 15.1 0 0 0 6.6 6.6l2.2-2.2a1 1 0 0 1 1-.25 11.4 11.4 0 0 0 3.6.57 1 1 0 0 1 1 1V20a1 1 0 0 1-1 1A17 17 0 0 1 3 4a1 1 0 0 1 1-1h3.5a1 1 0 0 1 1 1c0 1.25.2 2.45.57 3.57a1 1 0 0 1-.25 1z"/></svg>
      719-555-0148
    </p>
    <p class="contact-row">
      <svg viewBox="0 0 24 24" aria-hidden="true"><path d="M2 5h20v14H2z M2 5l10 8 10-8" fill="var(--navy)"/><path d="M3 6l9 7 9-7" fill="none" stroke="#fff" stroke-width="1.5"/></svg>
      dana@SMGarlic.com
    </p>
  </div>

  <div class="address">
    <p>P.O. Box 48 Larkton</p>
    <p>CO&nbsp; 80912</p>
  </div>

  <svg class="footer-band" viewBox="0 0 617 36" aria-hidden="true">
    <polygon points="0,14 215,14 211,21 0,21" fill="var(--red)"/>
    <polygon points="217,14 356,14 352,21 213,21" fill="var(--yellow)"/>
    <polygon points="377,0 617,0 617,36 352,36" fill="var(--navy)"/>
  </svg>
  <p class="website">www.SMGarlic.com</p>
</section>

<section class="card card-back" aria-label="Business card back">
  <div class="back-panel"></div>
  <div class="garlic-art" role="img" aria-label="Large yellow garlic bulb illustration with navy clove lines"></div>
  <div class="back-brand">
    <span class="primary">Sky Mesa</span>
    <span class="secondary">Gourmet Garlic</span>
  </div>
  <div class="social" aria-label="Social media links">
    <span class="social-dot"></span>
    <span class="social-dot"></span>
    <span class="social-dot"></span>
    <span class="social-dot"></span>
  </div>
</section>

</body>
</html>
```